Dietitian needs awesome business card

I need a contemporary design that's eye catching but professional.
My card is to given to doctors, specialists and patients alike.
I manage patients with chronic diseases
I have uploaded my logo and current business card, I would also like the other Certified Clinical Nutritionist logo incorporated into the design

Target Market(s)

Doctors, specialists and patients

Industry/Entity Type

Healthcare

Contact Information for Business Card

www.brightfieldnutrition.com.au
Ph: 0427 561 903
Fax: 6457 2183
email: marcus.k.diet@fernmail.com
Space on the back of the card with: Appointment date, Appointment time and appointment location

Font styles to use
Serif

Colors
fbee3e
876aae
ffc214

Requirements
Must have
• My Logo
• Certified Clinical Nutritionist Logo
• My 4 locations - Pinebrook Medical Centre, North Corrin Health, Hollis Medical, Ashcombe Doctors Surgery
Nice to have
• I like the colours in my current business card

```html
<!DOCTYPE html>
<html lang="en">
<head>
<meta charset="utf-8">
<title>Brightfield Nutrition &amp; Dietetics – Business Card</title>
<link href="https://fonts.googleapis.com/css2?family=Questrial&family=Arimo:wght@400;700&display=swap" rel="stylesheet">
<style>
  :root{
    --bg:#2e2f31;
    --card:#ffffff;
    --blue:#1f4fa3;
    --blue-deep:#143a85;
    --blue-light:#3f7fd0;
    --green:#8cc63f;
    --grey:#5b5e63;
    --rule:#c9ccd2;
    --orange:#f26a1f;
    --dots:#6d7fbf;
  }
  *{box-sizing:border-box;margin:0;padding:0}
  html,body{width:1200px;height:843px;overflow:hidden;background:var(--bg)}
  body{position:relative;font-family:"Arimo",Arial,sans-serif}
  .card{
    position:absolute;top:262px;width:540px;height:330px;background:var(--card);
    border-radius:3px;overflow:hidden;
  }
  .card--front{left:40px}
  .card--back{left:620px}

  /* front */
  .side-band{
    position:absolute;left:40px;top:95px;width:62px;height:235px;
    background:linear-gradient(180deg,var(--blue-light),var(--blue-deep));
  }
  .side-band svg{position:absolute;left:19px;width:24px;height:24px;fill:#fff}
  .brand-mark{
    position:absolute;left:34px;top:36px;width:74px;height:74px;border-radius:50%;
    background:var(--blue);
  }
  .brand{position:absolute;left:122px;top:42px}
  .brand__name{font-family:"Questrial",sans-serif;font-size:50px;line-height:1;color:var(--blue);letter-spacing:-.5px}
  .brand__tag{font-family:"Questrial",sans-serif;font-size:21px;color:var(--green);margin-top:2px}
  .person{position:absolute;left:124px;top:158px}
  .person__name{font-weight:700;font-size:21px;color:var(--blue)}
  .person__role{font-weight:700;font-size:15px;color:var(--green);margin-top:3px}
  .contact{position:absolute;left:124px;top:222px;list-style:none;color:var(--grey);font-size:14px;line-height:20px}
  .faint-circle{
    position:absolute;right:-40px;top:110px;width:260px;height:260px;border-radius:50%;
    background:#eef2ea;
  }

  /* back */
  .back-mark{position:absolute;left:28px;top:40px;width:50px;height:50px;border-radius:50%;background:var(--blue)}
  .badge{position:absolute;right:26px;top:16px;width:120px;height:50px;background:var(--orange)}
  .rule{position:absolute;left:96px;right:26px;height:1px;background:var(--rule)}
  .field{position:absolute;font-size:15px;color:var(--blue);display:flex;align-items:flex-end;gap:6px}
  .field__fill{flex:1;border-bottom:2px dotted var(--dots);height:14px}
  .field--time{left:300px;right:26px;top:130px}
  .field--date{left:28px;right:26px;top:206px}
  .ampm{font-size:11px}
  .locations{position:absolute;left:28px;top:240px;right:20px;display:grid;grid-template-columns:1fr 1fr;row-gap:8px;list-style:none;color:var(--grey);font-size:15px}
  .locations li{display:flex;align-items:center;gap:8px}
  .box{width:12px;height:12px;border:1.5px solid var(--blue)}
</style>
</head>
<body>

<section class="card card--front">
  <div class="faint-circle"></div>
  <div class="side-band">
    <svg style="top:95px" viewBox="0 0 24 24"><circle cx="12" cy="7" r="5"/><path d="M3 23c0-6 4-9 9-9s9 3 9 9z"/></svg>
    <svg style="top:128px" viewBox="0 0 24 24"><path d="M6 2l4 4-2 3c1 3 4 6 7 7l3-2 4 4-3 4C10 22 2 14 2 5z"/></svg>
    <svg style="top:158px" viewBox="0 0 24 24"><path d="M2 5h20v14H2z"/><path d="M2 5l10 8 10-8" stroke="#1f4fa3" stroke-width="2" fill="none"/></svg>
    <svg style="top:188px" viewBox="0 0 24 24"><circle cx="12" cy="12" r="10"/><path d="M2 12h20M12 2c-4 5-4 15 0 20M12 2c4 5 4 15 0 20" stroke="#1f4fa3" stroke-width="1.5" fill="none"/></svg>
  </div>
  <div class="brand-mark"></div>
  <div class="brand">
    <div class="brand__name">Brightfield</div>
    <div class="brand__tag">Nutrition &amp; Dietetics</div>
  </div>
  <div class="person">
    <div class="person__name">Marcus Kellaway</div>
    <div class="person__role">Nutritionist &amp; Chef</div>
  </div>
  <ul class="contact">
    <li>0427 561 903</li>
    <li>6457 2183</li>
    <li>marcus.k.diet@fernmail.com</li>
    <li>brightfieldnutrition.com.au</li>
  </ul>
</section>

<section class="card card--back">
  <div class="back-mark"></div>
  <div class="badge" role="img" aria-label="Certified Clinical Nutritionist badge"></div>
  <div class="rule" style="top:92px"></div>
  <div class="rule" style="top:120px"></div>
  <div class="field field--time">Time :<span class="field__fill"></span><span class="ampm">AM/PM</span></div>
  <div class="rule" style="top:176px"></div>
  <div class="field field--date">Date :<span class="field__fill"></span></div>
  <ul class="locations">
    <li><span class="box"></span>Pinebrook Medical Centre</li>
    <li><span class="box"></span>Ashcombe Doctors Surgery</li>
    <li><span class="box"></span>North Corrin Health</li>
    <li><span class="box"></span>Hollis Medical</li>
  </ul>
</section>

</body>
</html>
```